3 Page Design for Ninth Bay Capital

We want a Home Page, About Page, and Products & Services Page for Ninth Bay Capital. Please refer to the attached docs for more info.
If done in Figma, would like Figma files that can easily be ported to Wordpress.

```html
<!DOCTYPE html>
<html lang="en">
<head>
<meta charset="utf-8">
<title>Ninth Bay Capital — Home</title>
<link href="https://fonts.googleapis.com/css2?family=Archivo:wght@600;700;800&family=Jost:wght@400;500&display=swap" rel="stylesheet">
<style>
:root{
  --bg:#faf8f4;
  --sand:#f1ece6;
  --gold:#8b7355;
  --maroon:#9b1b30;
  --ink:#2a2a2a;
  --dark:#2b2b2b;
  --darker:#222;
  --white:#fff;
  --line1:#c9c0b4;
  --line2:#9a9186;
  --line3:#5c5750;
}
*{box-sizing:border-box;margin:0;padding:0}
html,body{width:1200px;height:3713px;overflow:hidden}
body{background:var(--bg);font-family:"Jost",sans-serif;color:var(--ink);position:relative}
.abs{position:absolute}
.heading{font-family:"Archivo",sans-serif;font-weight:700;color:var(--gold);letter-spacing:-0.5px;text-transform:uppercase}
.divider{display:flex;gap:8px}
.divider span{display:block;width:38px;height:3px}
.divider span:nth-child(1){background:var(--line1)}
.divider span:nth-child(2){background:var(--line2)}
.divider span:nth-child(3){background:var(--line3)}
.btn{display:inline-flex;align-items:center;gap:14px;background:var(--maroon);color:var(--white);font-size:14px;font-weight:500;text-transform:uppercase;border-radius:24px;padding:0 24px;height:42px;text-decoration:none;white-space:nowrap}
.btn svg{width:22px;height:10px}
p{font-size:15px;line-height:34px}

/* header */
.brand{left:150px;top:30px;font-family:"Jost",sans-serif;font-weight:500;font-size:20px;color:var(--ink);display:flex;align-items:center;gap:10px}
.brand i{display:block;width:16px;height:16px;border-radius:50%;background:var(--gold)}
.nav{left:442px;top:33px;display:flex;gap:36px;font-size:14px;text-transform:uppercase}
.nav a{color:var(--ink);text-decoration:none}
.nav a.active{color:#a8a8a8}
.nav-cta{left:935px;top:23px;height:36px;font-size:13px;padding:0 20px}

/* hero */
.hero{left:111px;top:81px;width:978px;height:478px;border-radius:16px;overflow:hidden;background:linear-gradient(90deg,#4a4c48 0%,#6b6e6a 45%,#8d928f 75%,#b3b8b6 100%)}
.hero-title{left:147px;top:266px;font-family:"Archivo",sans-serif;font-weight:700;font-size:33px;line-height:50px;color:#eee6da;text-transform:uppercase}
.hero-text{left:147px;top:378px;width:420px;color:#fff;font-size:15px;line-height:32px}
.hero-btn{left:147px;top:469px}

/* services */
.svc-title{left:0;width:1200px;top:635px;text-align:center;font-size:38px}
.svc-div{left:536px;top:698px}
.card-img{width:304px;height:387px;top:765px}
.card-img.r1{border-radius:14px}
.card-img.r2{border-radius:152px 152px 14px 14px}
.card-img.r3{border-radius:14px 200px 14px 14px}
.card-title{top:1197px;font-family:"Archivo",sans-serif;font-weight:700;font-size:20px;color:var(--maroon);text-transform:uppercase;letter-spacing:-0.3px}
.card-text{top:1240px;width:300px;font-size:15px}
.svc-btn{left:489px;top:1378px}

/* mission */
.mission{left:0;top:1506px;width:1200px;height:942px;background:var(--sand)}
.mis-title{left:0;width:1200px;top:1563px;text-align:center;font-size:38px}
.mis-div{left:536px;top:1627px}
.mis-text{left:130px;width:940px;top:1664px;text-align:center;font-size:15px}
.pill{left:111px;width:275px;height:84px;border-radius:10px;background:var(--white);display:flex;align-items:center;gap:26px;padding-left:22px;font-size:18px;text-transform:uppercase}
.pill.on{background:#ebe5de;border:1px solid #bfb6ab}
.pill svg{width:54px;height:54px}
.mis-img{left:438px;top:1777px;width:650px;height:358px;border-radius:14px;background:linear-gradient(135deg,#3a3d42 0%,#222428 60%,#15171a 100%)}
.mis-body{left:438px;top:2172px;width:640px}
.mis-btn{left:438px;top:2338px}

/* about */
.about-img{left:118px;top:2532px;width:386px;height:529px;border-radius:20px 20px 20px 20px;overflow:hidden}
.about-img .photo{position:absolute;left:0;top:0;width:386px;height:529px;border-radius:20px 0 330px 20px;background:linear-gradient(90deg,#cfd3d6 0%,#e6e8ea 45%,#bfc4c8 100%);border-right:8px solid var(--maroon);border-bottom:8px solid var(--maroon)}
.about-title{left:616px;top:2523px;font-size:38px}
.about-div{left:616px;top:2585px}
.about-text{left:616px;top:2621px;width:470px}
.about-text p+p{margin-top:16px}
.about-btn{left:616px;top:3013px}

/* cta + footer */
.footer{left:0;top:3258px;width:1200px;height:455px;background:var(--dark)}
.cta{left:111px;top:3141px;width:978px;height:238px;border-radius:20px;background:var(--gold)}
.cta-title{left:157px;top:3190px;font-family:"Archivo",sans-serif;font-weight:700;font-size:27px;color:#fff;text-transform:uppercase;letter-spacing:-0.5px}
.cta-text{left:160px;top:3241px;width:600px;color:#fff;font-size:15px;line-height:34px}
.cta-btn{left:871px;top:3239px}
.f-brand{left:140px;top:3480px;width:270px;text-align:center;color:#fff}
.f-brand .name{font-family:"Archivo",sans-serif;font-weight:700;font-size:22px;text-transform:uppercase}
.f-brand .tag{font-size:8px;letter-spacing:3px;text-transform:uppercase;margin-top:2px}
.f-col{top:3437px;list-style:none;color:#fff;font-size:15px;line-height:35px}
.copyright{left:0;top:3652px;width:1200px;height:61px;background:var(--darker);color:#fff;font-size:15px;text-align:center;line-height:61px}
</style>
</head>
<body>

<header>
  <div class="abs brand"><i></i>Ninth Bay Capital</div>
  <nav class="abs nav">
    <a class="active" href="#">Home</a><a href="#">About</a><a href="#">Products &amp; Services</a><a href="#">Contact Us</a>
  </nav>
  <a class="abs btn nav-cta" href="#">Get in touch <svg viewBox="0 0 22 10"><path d="M0 5h20M16 1l4 4-4 4" stroke="#fff" stroke-width="1.5" fill="none"/></svg></a>
</header>

<section>
  <div class="abs hero" role="img" aria-label="Athlete in a suit holding a football and a tablet in a modern office"></div>
  <h1 class="abs hero-title">Where discipline<br>meets wealth.</h1>
  <p class="abs hero-text">From peak performance to powerful legacy — we guide athletes into their financial next chapter.</p>
  <a class="abs btn hero-btn" href="#">Start your transition <svg viewBox="0 0 22 10"><path d="M0 5h20M16 1l4 4-4 4" stroke="#fff" stroke-width="1.5" fill="none"/></svg></a>
</section>

<section>
  <h2 class="abs heading svc-title">Ninth Bay Services</h2>
  <div class="abs divider svc-div"><span></span><span></span><span></span></div>

  <div class="abs card-img r1" style="left:111px;background:linear-gradient(160deg,#c9cdd1,#6f7a86 70%,#3d4550)" role="img" aria-label="Hand pointing a pen at financial charts on a laptop"></div>
  <div class="abs card-img r2" style="left:448px;background:linear-gradient(180deg,#b8c3cc,#6a7886 60%,#1e2a3a)" role="img" aria-label="Team working with robotic arms in an automation lab"></div>
  <div class="abs card-img r3" style="left:785px;background:linear-gradient(135deg,#8a6a4a,#4a3524 70%,#2b1e15)" role="img" aria-label="Keypad door lock on a wooden door"></div>

  <h3 class="abs card-title" style="left:110px">Wealth Blueprint™</h3>
  <h3 class="abs card-title" style="left:447px">Ninth Bay Automation</h3>
  <h3 class="abs card-title" style="left:784px">Legacy Anchor™</h3>

  <p class="abs card-text" style="left:112px">Your financial playbook starts here. We design a personalized wealth blueprint to align your current income, values</p>
  <p class="abs card-text" style="left:449px">Your money should work smarter than you do. We build automated systems that grow your wealth while you live your life</p>
  <p class="abs card-text" style="left:786px">We help you turn success into significance. The Legacy Anchor™ strategy ensures your wealth impacts the next generation</p>

  <a class="abs btn svc-btn" href="#">View more services <svg viewBox="0 0 22 10"><path d="M0 5h20M16 1l4 4-4 4" stroke="#fff" stroke-width="1.5" fill="none"/></svg></a>
</section>

<section>
  <div class="abs mission"></div>
  <h2 class="abs heading mis-title">Ninth Bay Mission</h2>
  <div class="abs divider mis-div"><span></span><span></span><span></span></div>
  <p class="abs mis-text">At Ninth Bay Capital, we believe your most important quarter happens off the field. Our mission is to empower high-performing athletes and entrepreneurs with the structure, strategy, and systems needed to build generational wealth.</p>

  <div class="abs pill on" style="top:1777px">
    <svg viewBox="0 0 54 54" fill="none" stroke="#9b1b30" stroke-width="2"><path d="M16 44V36c-4-3-6-8-6-13 0-9 7-15 16-15s15 6 15 14l4 7h-4v8h-7v7"/><circle cx="26" cy="22" r="6"/><circle cx="26" cy="22" r="2"/></svg>
    Clarity
  </div>
  <div class="abs pill" style="top:1895px">
    <svg viewBox="0 0 54 54" fill="none" stroke="#9b1b30" stroke-width="2"><circle cx="27" cy="27" r="15"/><circle cx="27" cy="27" r="21" stroke-dasharray="6 5"/><path d="M20 27l5 5 9-10"/></svg>
    Control
  </div>
  <div class="abs pill" style="top:2003px">
    <svg viewBox="0 0 54 54" fill="none" stroke="#9b1b30" stroke-width="2"><circle cx="14" cy="12" r="6"/><path d="M6 46h42M10 46V22h10v24M24 46V32h10v14M38 46V26h8v20M42 18v-8M38 14l4-4 4 4"/></svg>
    Compounding
  </div>

  <div class="abs mis-img" role="img" aria-label="Businessman and family standing around a glass table in a dark room"></div>
  <p class="abs mis-body">Your athletic peak may be measured in minutes on the clock — but your true potential lasts a lifetime. We built Ninth Bay Capital for the moment the game slows down, but your ambition doesn't. Our mission is to transform high-performance careers into generational wealth through strategy, automation, and mindset mastery.</p>
  <a class="abs btn mis-btn" href="#">Learn more <svg viewBox="0 0 22 10"><path d="M0 5h20M16 1l4 4-4 4" stroke="#fff" stroke-width="1.5" fill="none"/></svg></a>
</section>

<section>
  <div class="abs about-img"><div class="photo" role="img" aria-label="Man in a dress shirt standing by tall office windows"></div></div>
  <h2 class="abs heading about-title">About Ninth Bay</h2>
  <div class="abs divider about-div"><span></span><span></span><span></span></div>
  <div class="abs about-text">
    <p>We understand what it takes to win at the highest level — the discipline, the sacrifice, the focus. But what happens when the stadium lights go dark? Ninth Bay Capital is where your next chapter begins.</p>
    <p>We combine the precision of financial strategy with the mindset mastery of championship performance — giving elite athletes and entrepreneurs a proven framework to build and protect their wealth beyond their playing days. Born from years of observing the financial challenges athletes face in transition, and the systems that enable entrepreneurs to scale wealth without chaos.</p>
  </div>
  <a class="abs btn about-btn" href="#">View more about us <svg viewBox="0 0 22 10"><path d="M0 5h20M16 1l4 4-4 4" stroke="#fff" stroke-width="1.5" fill="none"/></svg></a>
</section>

<footer>
  <div class="abs footer"></div>
  <div class="abs cta"></div>
  <h2 class="abs cta-title">Ready to build your next chapter?</h2>
  <p class="abs cta-text">Transition with clarity. Automate your wealth. Create the legacy you've earned. Whether you're nearing the end of your professional career or looking to elevate your financial life — we'll help you turn momentum into meaning.</p>
  <a class="abs btn cta-btn" href="#">Start now <svg viewBox="0 0 22 10"><path d="M0 5h20M16 1l4 4-4 4" stroke="#fff" stroke-width="1.5" fill="none"/></svg></a>

  <div class="abs f-brand"><div class="name">Ninth Bay Capital</div><div class="tag">Your next chapter starts now</div></div>
  <ul class="abs f-col" style="left:555px"><li>Home</li><li>About</li><li>Products &amp; Services</li><li>Start Your Transition</li><li>Contact</li></ul>
  <ul class="abs f-col" style="left:847px"><li>Why Ninth Bay?</li><li>The Wealth Blueprint™ Method</li><li>Legacy Anchor™</li><li>FAQ</li><li>Blog (optional future)</li></ul>
  <div class="abs copyright">© 2025 Ninth Bay Capital. All Rights Reserved.</div>
</footer>

</body>
</html>
```